hi
would like the design about the some. just with our  details and logo
office number 01632960482
Mobil number 07700900317
web tidalbroom.ltd
email tidalbroom@postnest.co.uk
on the back we would like to put a price list

```html
<!DOCTYPE html>
<html lang="en">
<head>
<meta charset="utf-8">
<title>Tidal Broom – Window Cleaning Flyer and Price List</title>
<link href="https://fonts.googleapis.com/css2?family=Anton&family=Archivo+Black&family=Montserrat:wght@400;500;600;700;800&display=swap" rel="stylesheet">
<style>
  :root{
    --navy:#27318f;
    --royal:#2f45b5;
    --brand-blue:#2a63c9;
    --sky:#4a90d9;
    --pink:#e6399b;
    --ink:#111111;
    --white:#ffffff;
    --panel-text:#e3e7ff;
    --row-1:#2b3592;
    --row-2:#1e63ad;
    --row-3:#3f86cc;
    --row-4:#55b2e0;
    --row-5:#8fc7e6;
    --price-line:#e4e7f0;
    --card-head:#8a9cb7;
  }
  *{box-sizing:border-box;margin:0;padding:0}
  html,body{width:815px;height:1200px;overflow:hidden;background:#fff}
  body{font-family:"Montserrat",sans-serif;color:var(--ink);position:relative}

  .sheet{position:absolute;top:325px;width:665px;height:940px;overflow:hidden;background:var(--white);transform:scale(.585);transform-origin:0 0;box-shadow:0 0 0 1px #eee}
  .sheet-front{left:12px}
  .sheet-back{left:414px}
  .shapes{position:absolute;inset:0}
  .abs{position:absolute}

  /* front */
  .brand{left:30px;top:26px}
  .brand-name{font-weight:800;font-size:44px;line-height:1;color:var(--brand-blue);letter-spacing:-.5px}
  .brand-sub{font-weight:500;font-size:15px;color:var(--navy);margin-top:8px}

  .headline{left:30px;top:424px;width:280px}
  .headline .big{font-family:"Archivo Black",sans-serif;font-size:46px;line-height:1;color:var(--ink)}
  .headline .mid{font-family:"Anton",sans-serif;font-size:33px;line-height:1.05;color:var(--navy);margin:3px 0 1px}
  .audience{left:0;top:562px;width:290px;height:40px;background:var(--pink);color:#fff;font-weight:700;font-size:11.5px;line-height:1.12;padding:7px 0 0 30px}

  .quote{left:30px;top:620px}
  .quote .q1{font-weight:800;font-size:22px;color:var(--brand-blue);line-height:1.05}
  .quote .q2{font-weight:800;font-size:19px;color:var(--ink);line-height:1.15}
  .contacts{left:30px;top:673px;list-style:none}
  .contacts li{display:flex;align-items:center;gap:9px;font-weight:700;font-size:13.5px;height:21.5px}
  .contacts svg{width:12px;height:12px;flex:none}
  .follow{left:30px;top:765px;font-weight:700;font-size:12.5px;color:var(--navy)}
  .social{left:30px;top:790px;display:flex;gap:9px}
  .social span{width:20px;height:20px;border-radius:50%;background:var(--royal)}
  .handle{left:30px;top:815px;font-weight:700;font-size:10.5px;color:var(--navy)}

  .tab{background:#fff;border-radius:0 12px 12px 0;font-weight:800;color:#8e95a8;font-size:16px;letter-spacing:.5px;padding:2px 0 0 16px;height:24px}
  .tab-about{left:328px;top:463px;width:140px}
  .tab-services{left:298px;top:571px;width:170px}
  .about{left:328px;top:497px;width:300px;color:var(--panel-text);font-size:8.6px;line-height:1.27}
  .about strong{display:block;color:#fff;font-weight:800;font-size:8.4px;margin-bottom:4px}

  .service{width:120px;text-align:center;color:#fff;font-weight:700;font-size:10.5px;line-height:1.15}
  .service svg{width:26px;height:26px;display:block;margin:0 auto 6px}
  .s1{left:282px;top:608px}
  .s2{left:399px;top:608px}
  .s3{left:525px;top:608px}
  .s4{left:339px;top:679px}
  .s5{left:462px;top:679px}

  .promise{left:310px;top:762px;width:320px;color:#fff;font-weight:800;font-size:13px;line-height:1.2}
  .promise em{font-style:normal;color:var(--pink)}

  .footer{left:0;top:856px;width:665px;text-align:center;color:#fff}
  .footer .cta{font-weight:800;font-size:16.5px;color:var(--pink);line-height:1.2}
  .footer p{font-weight:500;font-size:15.5px;line-height:1.25}

  /* back */
  .price-title{left:0;top:24px;width:665px;text-align:center;font-family:"Archivo Black",sans-serif;font-size:37px;color:#fff;letter-spacing:.5px}
  .price-heading{left:0;top:246px;width:665px;text-align:center;font-weight:800;font-size:16.5px;letter-spacing:1.6px;color:var(--brand-blue)}
  .house-row{left:30px;width:359px;height:77px;display:flex;align-items:center;justify-content:center;color:#fff;font-weight:700;font-size:15px;border-radius:2px}
  .r1{top:272px;background:var(--row-1)}
  .r2{top:354px;background:var(--row-2)}
  .r3{top:435px;background:var(--row-3)}
  .r4{top:517px;background:var(--row-4)}
  .r5{top:599px;background:var(--row-5)}
  .extras{left:396px;width:239px;font-size:9.5px;text-align:center}
  .extras .visit{height:21px;background:#151515;color:var(--pink);font-weight:700;font-size:10.5px;line-height:21px;border-radius:2px}
  .extras .line{height:17px;line-height:17px;margin-top:1.7px;background:var(--price-line);color:#222;font-weight:500}
  .e1{top:272px}.e2{top:354px}.e3{top:435px}.e4{top:517px}.e5{top:599px}

  .other{left:34px;top:695px;width:601px;height:150px;border:1.5px solid var(--pink);border-radius:3px}
  .other-title{left:0;top:685px;width:665px;text-align:center}
  .other-title span{background:#fff;padding:0 10px;font-weight:800;font-size:16.5px;letter-spacing:1.4px;color:var(--pink)}
  .card{top:712px;width:168px;text-align:center}
  .card-head{height:65px;background:var(--card-head);color:#eef1f8;font-weight:700;font-size:10.5px;line-height:1.15;padding-top:13px;border-radius:2px}
  .card-head b{display:block;color:var(--navy);font-size:9px;margin-top:4px}
  .card .line{height:20px;line-height:20px;margin-top:4px;background:var(--price-line);font-size:9px;font-weight:500;color:#222;border-radius:2px}
  .c1{left:47px}.c2{left:247px}.c3{left:449px}
</style>
</head>
<body>

<section class="sheet sheet-front" aria-label="Flyer front">
  <svg class="shapes" width="665" height="940" viewBox="0 0 665 940">
    <defs>
      <linearGradient id="photoTone" x1="0" y1="0" x2="1" y2="1">
        <stop offset="0" stop-color="#5b5f66"/><stop offset=".35" stop-color="#d9d5cc"/>
        <stop offset=".7" stop-color="#eeeae2"/><stop offset="1" stop-color="#8fa3c6"/>
      </linearGradient>
      <linearGradient id="panelTone" x1="0" y1="0" x2="0" y2="1">
        <stop offset="0" stop-color="#3b5fd0"/><stop offset=".45" stop-color="#2a3aa6"/><stop offset="1" stop-color="#252b8a"/>
      </linearGradient>
      <linearGradient id="silver" x1="0" y1="0" x2="1" y2="0">
        <stop offset="0" stop-color="#8e96a3"/><stop offset=".5" stop-color="#e8ebf0"/><stop offset="1" stop-color="#9aa2ae"/>
      </linearGradient>
      <linearGradient id="gutterTone" x1="0" y1="0" x2="1" y2="1">
        <stop offset="0" stop-color="#6a6f72"/><stop offset=".5" stop-color="#5b4a34"/><stop offset="1" stop-color="#e98a3c"/>
      </linearGradient>
      <linearGradient id="glassTone" x1="0" y1="0" x2="1" y2="1">
        <stop offset="0" stop-color="#e9f2fb"/><stop offset=".5" stop-color="#9fc4e4"/><stop offset="1" stop-color="#e6c53a"/>
      </linearGradient>
    </defs>
    <path role="img" aria-label="Photo: window cleaner in blue uniform cleaning a house gutter"
      fill="url(#photoTone)" d="M0,140 C150,150 320,120 410,0 L665,0 L665,320 C560,390 440,410 330,395 C220,380 100,320 0,330 Z"/>
    <path fill="var(--pink)" d="M0,108 C130,124 300,104 400,18 C345,112 220,150 0,150 Z"/>
    <path fill="var(--sky)" d="M345,132 C415,92 458,42 478,0 L505,0 C478,62 420,112 345,132 Z"/>
    <path fill="url(#panelTone)" d="M665,300 C560,390 420,430 330,450 C300,470 290,520 288,580 C286,680 292,780 300,880 L665,880 Z"/>
    <path fill="url(#silver)" d="M0,330 C100,320 220,380 330,395 C420,408 500,400 560,380 C480,425 400,432 320,422 C210,408 100,360 0,365 Z"/>
    <circle cx="394" cy="377" r="80" fill="#fff"/>
    <circle role="img" aria-label="Photo: gloved hand clearing leaves from a gutter" cx="394" cy="377" r="73" fill="url(#gutterTone)" stroke="#c7ccd5" stroke-width="3"/>
    <circle cx="540" cy="327" r="100" fill="#fff"/>
    <circle role="img" aria-label="Photo: gloved hand wiping a window with a cloth and spray bottle" cx="540" cy="327" r="93" fill="url(#glassTone)" stroke="#c7ccd5" stroke-width="3"/>
    <path fill="url(#silver)" d="M0,862 C180,828 460,822 665,845 L665,866 C460,846 200,852 0,884 Z"/>
    <path fill="#0b0b0b" d="M0,884 C200,852 460,846 665,866 L665,940 L0,940 Z"/>
  </svg>

  <div class="abs brand">
    <div class="brand-name">TIDAL BROOM</div>
    <div class="brand-sub">CLEANING &amp; MAINTENANCE LTD</div>
  </div>

  <div class="abs headline">
    <div class="big">RELIABLE</div>
    <div class="mid">WINDOW CLEANING</div>
    <div class="big">SERVICES</div>
  </div>
  <div class="abs audience">FOR RESIDENTIAL AND COMMERCIAL<br>CUSTOMERS IN AND AROUND ESSEX.</div>

  <div class="abs quote">
    <div class="q1">FOR A FREE QUOTE</div>
    <div class="q2">PLEASE CONTACT US</div>
  </div>
  <ul class="abs contacts">
    <li><svg viewBox="0 0 16 16"><rect x="2" y="6" width="12" height="8" rx="1.5" fill="var(--brand-blue)"/><path d="M1 6c2-4 12-4 14 0" stroke="var(--brand-blue)" stroke-width="2" fill="none"/></svg>01632960482</li>
    <li><svg viewBox="0 0 16 16"><path d="M3 1l3 1 1 4-2 1c1 2 2 3 4 4l1-2 4 1 1 3-2 2C7 15 1 9 1 3z" fill="var(--brand-blue)"/></svg>07700900317</li>
    <li><svg viewBox="0 0 16 16"><rect x="1" y="3" width="14" height="10" rx="1" fill="var(--brand-blue)"/><path d="M1 4l7 5 7-5" stroke="#fff" stroke-width="1.4" fill="none"/></svg>tidalbroom@postnest.co.uk</li>
    <li><svg viewBox="0 0 16 16"><circle cx="8" cy="8" r="6.5" fill="none" stroke="var(--brand-blue)" stroke-width="1.5"/><ellipse cx="8" cy="8" rx="2.6" ry="6.5" fill="none" stroke="var(--brand-blue)" stroke-width="1.2"/><path d="M1.5 8h13" stroke="var(--brand-blue)" stroke-width="1.2"/></svg>www.tidalbroom.ltd</li>
  </ul>
  <div class="abs follow">FOLLOW US ON SOCIAL MEDIA</div>
  <div class="abs social"><span></span><span></span><span></span></div>
  <div class="abs handle">@TidalBroomCleaningLTD</div>

  <div class="abs tab tab-about">ABOUT US</div>
  <div class="abs about">
    <strong>RESIDENTIAL AND COMMERCIAL WINDOW CLEANING IN ESSEX.</strong>
    Window Cleaning Essex Tidal Broom Cleaning Ltd have been cleaning windows for commercial and residential properties throughout Hutton, Shenfield and the surrounding areas since 1999. We cover most towns in Essex including Brentwood, Chelmsford, Romford, Loughton and Billericay.
  </div>

  <div class="abs tab tab-services">OUR SERVICES</div>
  <div class="abs service s1">
    <svg viewBox="0 0 34 34"><circle cx="17" cy="17" r="15" fill="none" stroke="#fff" stroke-width="1.6"/><rect x="11" y="9" width="12" height="16" fill="none" stroke="#fff" stroke-width="1.6"/><path d="M17 9v16M11 17h12" stroke="#fff" stroke-width="1.4"/></svg>
    WINDOW<br>CLEANING
  </div>
  <div class="abs service s2">
    <svg viewBox="0 0 34 34"><circle cx="17" cy="17" r="15" fill="none" stroke="#fff" stroke-width="1.6"/><path d="M9 24h16M11 24v-7l6-5 6 5v7M17 12v12" stroke="#fff" stroke-width="1.5" fill="none"/></svg>
    CONSERVATORY<br>CLEANING
  </div>
  <div class="abs service s3">
    <svg viewBox="0 0 34 34"><circle cx="17" cy="17" r="15" fill="none" stroke="#fff" stroke-width="1.6"/><path d="M10 20h8l3-4h4M12 20v4M23 13l3-2M23 16h4M23 19l3 2" stroke="#fff" stroke-width="1.5" fill="none"/></svg>
    PRESSURE<br>WASHING
  </div>
  <div class="abs service s4">
    <svg viewBox="0 0 34 34"><circle cx="17" cy="17" r="15" fill="none" stroke="#fff" stroke-width="1.6"/><path d="M10 10h14v4H10zM13 14v12M21 14v12" stroke="#fff" stroke-width="1.5" fill="none"/></svg>
    GUTTER<br>CLEANING
  </div>
  <div class="abs service s5">
    <svg viewBox="0 0 34 34"><circle cx="17" cy="17" r="15" fill="none" stroke="#fff" stroke-width="1.6"/><path d="M9 17l8-7 8 7M12 15v9h10v-9" stroke="#fff" stroke-width="1.5" fill="none"/></svg>
    SOFFIT'S &amp; FASCIA<br>CLEANING
  </div>

  <div class="abs promise">WE ARE HAPPY TO PROVIDE <em>FREE, FRIENDLY ADVICE</em> AND AN ON SITE DEMONSTRATION OF OUR WINDOW CLEANING CAPABILITIES.</div>

  <div class="abs footer">
    <div class="cta">USE ‘CONTACT US’ FORM</div>
    <p>on our web site &amp; add images of your property,<br>we will then provide a quote with-in 48 Hours.</p>
  </div>
</section>

<section class="sheet sheet-back" aria-label="Flyer back: price list">
  <svg class="shapes" width="665" height="940" viewBox="0 0 665 940">
    <defs>
      <linearGradient id="silverBack" x1="0" y1="0" x2="1" y2="0">
        <stop offset="0" stop-color="#8e96a3"/><stop offset=".5" stop-color="#e8ebf0"/><stop offset="1" stop-color="#9aa2ae"/>
      </linearGradient>
      <linearGradient id="officeTone" x1="0" y1="0" x2="0" y2="1">
        <stop offset="0" stop-color="#8a6f5c"/><stop offset=".6" stop-color="#6b5b52"/><stop offset="1" stop-color="#9aa0a8"/>
      </linearGradient>
      <linearGradient id="lawnTone" x1="0" y1="0" x2="0" y2="1">
        <stop offset="0" stop-color="#5da0e0"/><stop offset=".5" stop-color="#8d5a44"/><stop offset="1" stop-color="#4f9a3a"/>
      </linearGradient>
      <linearGradient id="roofTone" x1="0" y1="0" x2="0" y2="1">
        <stop offset="0" stop-color="#dfe6ee"/><stop offset=".6" stop-color="#9b5a5a"/><stop offset="1" stop-color="#cfd6de"/>
      </linearGradient>
    </defs>
    <path fill="var(--pink)" d="M0,0 H665 V108 C560,110 450,142 332,148 C215,142 105,110 0,108 Z"/>
    <path fill="url(#silverBack)" d="M10,112 C80,110 140,122 175,150 C130,134 70,126 10,112 Z"/>
    <path fill="url(#silverBack)" d="M655,112 C585,110 525,122 490,150 C535,134 595,126 655,112 Z"/>
    <circle cx="153" cy="149" r="74" fill="#fff"/>
    <circle role="img" aria-label="Photo: office building with large windows" cx="153" cy="149" r="68" fill="url(#officeTone)" stroke="#c7ccd5" stroke-width="3"/>
    <circle cx="323" cy="149" r="74" fill="#fff"/>
    <circle role="img" aria-label="Photo: brick house with lawn under blue sky" cx="323" cy="149" r="68" fill="url(#lawnTone)" stroke="#c7ccd5" stroke-width="3"/>
    <circle cx="495" cy="149" r="74" fill="#fff"/>
    <circle role="img" aria-label="Photo: house front with conservatory roof" cx="495" cy="149" r="68" fill="url(#roofTone)" stroke="#c7ccd5" stroke-width="3"/>
    <path fill="url(#silverBack)" d="M0,866 C180,832 460,826 665,849 L665,870 C460,850 200,856 0,888 Z"/>
    <path fill="#0b0b0b" d="M0,888 C200,856 460,850 665,870 L665,940 L0,940 Z"/>
  </svg>

  <div class="abs price-title">OUR PRODUCT PRICE LIST</div>
  <div class="abs price-heading">RELIABLE WINDOW CLEANING SERVICE PRICES</div>

  <div class="abs house-row r1">SEMI DETACHED (3/4 BED)</div>
  <div class="abs house-row r2">DETACHED (3/4 BED)</div>
  <div class="abs house-row r3">DETACHED (5 BED)</div>
  <div class="abs house-row r4">TERRACE (FRONT ONLY)</div>
  <div class="abs house-row r5">TERRACE (FRONT AND BACK)</div>

  <div class="abs extras e1"><div class="visit">FROM £14 PER VISIT</div><div class="line">+ Conservatory roofs from £60.00</div><div class="line">+ Drives from £120.00</div><div class="line">+ Gutters from £60.00</div></div>
  <div class="abs extras e2"><div class="visit">FROM £16 PER VISIT</div><div class="line">+ Conservatory roofs from £60.00</div><div class="line">+ Drives from £120.00</div><div class="line">+ Gutters from £60.00</div></div>
  <div class="abs extras e3"><div class="visit">FROM £23 PER VISIT</div><div class="line">+ Conservatory roofs from £60.00</div><div class="line">+ Drives from £120.00</div><div class="line">+ Gutters from £60.00</div></div>
  <div class="abs extras e4"><div class="visit">FROM £10 PER VISIT</div><div class="line">+ Conservatory roofs from £60.00</div><div class="line">+ Drives from £120.00</div><div class="line">+ Gutters from £60.00</div></div>
  <div class="abs extras e5"><div class="visit">FROM £14 PER VISIT</div><div class="line">+ Conservatory roofs from £60.00</div><div class="line">+ Drives from £120.00</div><div class="line">+ Gutters from £60.00</div></div>

  <div class="abs other"></div>
  <div class="abs other-title"><span>OTHER CLEANING SERVICES</span></div>
  <div class="abs card c1">
    <div class="card-head">CONSERVATORY ROOF<br>CLEANING<b>FROM £60 PER VISIT</b></div>
    <div class="line">+ Drives from £120.00</div>
    <div class="line">+ Gutters from £60.00</div>
  </div>
  <div class="abs card c2">
    <div class="card-head">DRIVEWAYS &amp; PATIO<br>CLEANING<b>FROM £120 PER VISIT</b></div>
    <div class="line">+ Conservatory roofs from £60.00</div>
    <div class="line">+ Gutters from £60.00</div>
  </div>
  <div class="abs card c3">
    <div class="card-head">GUTTER CLEANING<br>&nbsp;<b>FROM £120 PER VISIT</b></div>
    <div class="line">+ Conservatory roofs from £60.00</div>
    <div class="line">+ Drives from £120.00</div>
  </div>

  <div class="abs footer" style="top:860px">
    <div class="cta">USE ‘CONTACT US’ FORM</div>
    <p>on our web site &amp; add images of your property,<br>we will then provide a quote with-in 48 Hours.</p>
  </div>
</section>

</body>
</html>
```